Coastal Learner Bureau business cards

Australian company about to start offering its services. We recruit international students to come to study English, vocational education and postgraduate courses in Australia. We help them find the institution and select the right city they want to come to Australia. We are a young, online oriented and supportive agency. Our clients are between 18 and 35 years old, mainly University students, young professionals or people with work experience. We provide much more information that any other agency offer. We administrate a Facebook group with more than 11.000 members that daily ask questions about general information when coming to Australia, while they are here and even after they leave the country

Target Market(s)

International students from South America, Central America and Europe

Industry/Entity Type

Student

Contact Information for Business Card

Tomas Bilbrea
Managing Director
tomas@kelvarin.com.au
www.kelvoria.com.au
+61 491058264
Melbourne, Australia

Font styles to use
Serif
Sans Serif

Colors

Designer to choose colors to be used in the design.

Requirements
Must have
• Horizontal design
• Standard business card size and shape. If font uses green or yellow colours, they will have to match the ones from the logo
Nice to have
• UPDATE: Use the contents of the green image to design one of the card sides. Use our logo in the background of that side as watermark.
• Passport image, or immigration stamps. A picture of the Yarra River (from Melbourne) would be cool as well.
Should not have
• Non-standard business card size and shape
• Not black as the background colour of any sides as we are not a VIP agency or a hight class service. We are orientes to young people and they like colours, pictures, something attractive.
• Vertical design
• NO YELLOW or BLACK AS THE BACKGROUND COLOUR OF ANY SIDE OF THE BIZ CARD

```html
<!DOCTYPE html>
<html lang="en">
<head>
<meta charset="utf-8">
<title>Coastal Learner Bureau – Business Cards</title>
<link rel="stylesheet" href="https://fonts.googleapis.com/css2?family=Arimo:wght@400;700&display=swap">
<style>
  :root {
    --green: #0d6b3f;
    --green-dark: #0a5a34;
    --yellow: #d9b10c;
    --white: #ffffff;
    --ink: #1b1b1b;
    --backdrop: #e9ebe9;
  }
  * { margin: 0; padding: 0; box-sizing: border-box; }
  html, body {
    width: 1200px; height: 997px; overflow: hidden;
    background: var(--backdrop);
    font-family: "Arimo", Arial, sans-serif;
  }
  .card {
    position: absolute;
    left: 240px;
    width: 720px; height: 410px;
    border-radius: 22px;
    overflow: hidden;
    box-shadow: 0 10px 30px rgba(0,0,0,.18);
  }
  .card-front { top: 40px; }
  .card-back  { top: 525px; background: var(--white); }
  .card-shapes { position: absolute; inset: 0; width: 100%; height: 100%; }

  .brand-name {
    position: absolute;
    font-weight: 700;
    white-space: nowrap;
  }
  .card-front .brand-name {
    left: 44px; top: 172px;
    font-size: 34px;
    color: var(--white);
  }
  .tagline {
    position: absolute;
    left: 330px; top: 306px;
    font-size: 17px; font-weight: 700;
    color: var(--green-dark);
  }

  .card-back .brand {
    position: absolute; left: 0; right: 0; top: 92px;
    display: flex; justify-content: center; align-items: center; gap: 12px;
  }
  .card-back .brand-name { position: static; font-size: 34px; color: var(--green-dark); }
  .brand-dot { width: 18px; height: 18px; border-radius: 50%; background: var(--yellow); }

  .person { position: absolute; left: 0; right: 0; top: 232px; text-align: center; }
  .person-name {
    font-size: 19px; font-weight: 700; letter-spacing: 1px;
    color: var(--green-dark);
  }
  .person-role { font-size: 14px; color: var(--ink); margin-top: 2px; }

  .website {
    position: absolute; right: 32px; top: 292px;
    font-size: 17px; font-weight: 700; letter-spacing: .5px;
    color: var(--yellow);
  }
  .contact-list { position: absolute; left: 26px; top: 348px; list-style: none; }
  .contact-item {
    display: flex; align-items: center; gap: 10px;
    font-size: 17px; color: var(--white);
    margin-bottom: 6px;
  }
  .contact-icon { width: 22px; height: 22px; }
</style>
</head>
<body>

<section class="card card-front" aria-label="Card front">
  <svg class="card-shapes" viewBox="0 0 720 410" preserveAspectRatio="none" aria-hidden="true">
    <rect width="720" height="410" fill="var(--yellow)"/>
    <path d="M0 0 H720 V140 H490 Q462 140 462 168 V226 Q462 252 436 252 H0 Z" fill="var(--green)"/>
  </svg>
  <p class="brand-name">Coastal Learner Bureau</p>
  <p class="tagline">Hacemos más por ti!</p>
</section>

<section class="card card-back" aria-label="Card back">
  <svg class="card-shapes" viewBox="0 0 720 410" preserveAspectRatio="none" aria-hidden="true">
    <rect y="222" width="720" height="120" fill="var(--yellow)"/>
    <path d="M0 335 H300 Q312 335 320 325 L348 282 Q354 274 366 274 H720 V410 H0 Z" fill="var(--green)"/>
  </svg>

  <div class="brand">
    <p class="brand-name">Coastal Learner Bureau</p>
    <span class="brand-dot"></span>
  </div>

  <div class="person">
    <p class="person-name">TOMAS BILBREA</p>
    <p class="person-role">Managing Director</p>
  </div>

  <p class="website">www.kelvoria.com.au</p>

  <ul class="contact-list">
    <li class="contact-item">
      <svg class="contact-icon" viewBox="0 0 22 22" aria-hidden="true">
        <circle cx="11" cy="11" r="11" fill="rgba(255,255,255,.35)"/>
        <path d="M7 6.5 Q6 7.5 6.6 9.4 Q8.4 13.8 12.8 15.4 Q14.6 16 15.5 15 L14 13.2 L12.4 13.8 Q10 12.6 8.9 10.1 L9.6 8.4 Z" fill="var(--white)"/>
      </svg>
      +61 491058264
    </li>
    <li class="contact-item">
      <svg class="contact-icon" viewBox="0 0 22 22" aria-hidden="true">
        <circle cx="11" cy="11" r="11" fill="rgba(255,255,255,.35)"/>
        <rect x="5.5" y="7" width="11" height="8" rx="1" fill="none" stroke="var(--white)" stroke-width="1.4"/>
        <path d="M5.8 7.5 L11 11.5 L16.2 7.5" fill="none" stroke="var(--white)" stroke-width="1.4"/>
      </svg>
      tomas@kelvarin.com.au
    </li>
  </ul>
</section>

</body>
</html>
```